Medical Learning Web Design Project

The web site will be a site for medical students. It is aimed at providing a collaborative place for students to study, learn, question each other and challenge each other with learning. The site needs to have a section on the page that is for the content and this needs to be relatively clean and clinical. The surrounding elements will be informative (for the statistics, challenge etc). There will also be a slide-out screen that allows for the social/friend elements of the site.

The colour scheme needs to be clean and clinical where appropriate, but also engaging and exciting for the social/competitive elements.
Updates

Just for clarity: The site isn't expected to be 'coded' ... it is just the layered PSD files that I need.

Also, with regards to the navigation buttons ... they will never ALL be present at the same time so don't feel the need to design all on one page, but creativity around allowing few or many on a page will be an advantage ...

Thanks

Hi,

Please note that the image uploaded has been done as a wireframe by the developers. I am looking for a more creative and engaging way of presenting that content ...

Thanks

Hi all

Thank you all for the designs so far ...!

Please have a look at the new uploaded file, I am also looking not just for a 'templated home page' but also some different layouts that are represented in these wireframes. If the various layouts represented can be condensed down into 1 or 2 page templates with appropriate colour schemes to capture the type of content on the page (as already mentioned ... social .. competitive ... learning), then that will help me live the concepts better too! The friends tab for instance I have envisaged as a slider covering the screen and then sliding back when complete ... but let me see what creativity you can give to this ...!

Many thanks

Reason: Just allowing for final tweaks ...

Target Market(s)

Medical Students

Industry/Entity Type

Medical

Requirements
Must have
• - Not cluttered appearance
- Dynamic navigation (ie. site will be developed to only show relevant navigation buttons on each page ...)
- Navigation buttons (need to be individual buttons) will be: 'Home', 'Take the tour', 'What your peers say', 'Subscriptions', 'Free Signup', 'Contact us', 'Moderation', 'Statistics', 'Competition', 'Answer Questions', 'Post Questions', 'My profile', 'Friends'
- Please also ensure it is engaging for social elements and competitive elements (perhaps slightly different design for pages focussed on each element)
- Please also ensure that there is a masculine design and feminine design that has continuity for the site but depending on gender the design can be tailored to be more appealing (that means perhaps male social design, male competitive design, female social design, female competitive design ... without loosing continuity through the site).
- Photoshop PSD format
- Pixel perfect at least 1000 pixels wide (but the design needs to allow for various monitor sizes (only desktop or laptops ... not tablets or smart phones)

```html
<!DOCTYPE html>
<html lang="en">
<head>
<meta charset="utf-8">
<title>Medvora – The Medical Peer Review</title>
<link href="https://fonts.googleapis.com/css2?family=Sorts+Mill+Goudy&family=Caveat:wght@500&family=Open+Sans:ital,wght@0,400;0,600;1,400&family=Arimo:wght@400;700&display=swap" rel="stylesheet">
<style>
:root{
  --header:#a3c1c9;
  --nav:#a9c6ce;
  --hero:#c3d9de;
  --body:#f1f1f1;
  --footer:#4b4b4b;
  --field:#6f8f98;
  --teal-text:#2f7c99;
  --heading-box:#6e7aa8;
  --heading-shadow:#b5b5b5;
  --dark:#333;
  --muted:#555;
  --photo-border:#8ba9b2;
  --white:#fff;
}
*{box-sizing:border-box;margin:0;padding:0}
html,body{width:1200px;height:1137px;overflow:hidden}
body{position:relative;background:var(--body);font-family:"Arimo",Arial,sans-serif;color:var(--dark)}
.abs{position:absolute}

/* header */
.site-header{left:0;top:0;width:1200px;height:183px;background:linear-gradient(#a8c6ce,var(--header))}
.brand{left:52px;top:28px;font-family:"Sorts Mill Goudy",serif;font-size:46px;color:var(--white);line-height:1}
.brand-rule{left:104px;top:107px;width:185px;height:2px;background:#8aa2a9}
.tagline{left:107px;top:114px;font-family:"Open Sans",sans-serif;font-size:15px;color:#4e6a73}
.quote{left:320px;top:38px;font-family:"Caveat",cursive;font-size:22px;color:#4e6a73}
.quote-source{right:360px;top:75px;font-family:"Open Sans",sans-serif;font-size:13px;color:#5e7b84}
.stats-line{left:0;width:1162px;text-align:center;top:137px;font-family:"Open Sans",sans-serif;font-style:italic;font-size:18px;color:var(--white)}
.social-icons{right:45px;top:12px;display:flex;gap:6px}
.social-icons span{width:20px;height:20px;border-radius:3px;background:#3c5f86;display:block}
.social-icons span:nth-child(3n+2){background:#2e8fb8}
.social-icons span:nth-child(5){background:#2d7d3d}
.social-icons span:last-child{background:#c86a1f}
.field{left:903px;width:251px;height:28px;background:var(--field);color:#0e2b33;font-size:13px;padding:6px 10px}
.remember{left:903px;top:128px;font-size:11.5px;color:#2c4a52;display:flex;align-items:center;gap:6px}
.remember i{width:13px;height:13px;border:1px solid #5a7a83;background:#c9dde1;display:block}
.forgot{left:904px;top:147px;font-size:11.5px;color:#2c4a52}
.login-btn{left:1091px;top:130px;width:62px;height:22px;background:linear-gradient(#95adb4,#6f8c94);color:var(--white);font-family:"Open Sans",sans-serif;font-size:14px;text-align:center;line-height:22px;border:1px solid #5f7b83}

/* nav */
.main-nav{left:0;top:183px;width:1200px;height:48px;background:var(--nav);border-top:1px solid #b8d0d6;box-shadow:0 2px 3px rgba(0,0,0,.15);display:flex;justify-content:center;align-items:center;gap:13px;font-family:"Sorts Mill Goudy",serif;font-size:21px;color:var(--white)}
.main-nav .sep{opacity:.9}

/* hero */
.hero{left:0;top:231px;width:1200px;height:494px;background:var(--hero);box-shadow:0 3px 6px rgba(0,0,0,.2)}
.news-flash{right:453px;top:253px;font-size:12.5px;color:#444}
.share-square{left:765px;top:245px;width:31px;height:31px;background:#3b5b94;border-radius:2px}
.share-btn{height:24px;border:1px solid #8ca2b8;border-radius:3px;background:linear-gradient(#f3f6fa,#d6dfe9);font-size:13px;font-weight:700;color:#3b5b94;padding:3px 8px;top:249px}
.count{top:251px;height:20px;border:1px solid #aaa;background:#fff;font-size:11.5px;padding:2px 4px;color:#333}
.hero-title{left:128px;top:356px;font-family:"Sorts Mill Goudy",serif;font-size:22px;color:#444}
.benefits{left:128px;top:420px;list-style:none;font-size:15px;color:var(--teal-text);line-height:36px}
.photo{border:2px solid var(--photo-border)}
.arrow{top:490px}

/* lower */
.box-head{height:36px;background:var(--heading-box);box-shadow:5px 5px 0 var(--heading-shadow);color:var(--white);font-family:"Open Sans",sans-serif;font-size:17px;padding:6px 11px}
.video{left:53px;top:830px;width:352px;height:218px;background:#2b2b2b}
.video-bar{left:53px;top:1033px;width:352px;height:15px;background:#d8d8d8;border-top:1px solid #aaa;font-size:9px;color:#333;display:flex;align-items:center;gap:8px;padding:0 6px}
.video-bar .track{flex:1;height:4px;background:#999;border-radius:2px}
.post{left:464px;width:304px;display:flex;gap:19px}
.cal{width:46px;flex:none}
.post p{font-size:12.5px;line-height:18.5px;color:#444;text-align:justify;width:239px}
.more{display:block;text-align:right;color:#3a5f9a;font-size:11.5px}
.rule{height:1px;background:#cfcfcf}
.join{left:609px;top:1034px;font-size:13px;color:#3a5f9a;display:flex;align-items:center;gap:8px}
.fans{left:837px;top:799px;font-size:12.5px;color:#444}
.fan{width:55px;height:55px;border:1px solid #333;background:#fff}
.fan-name{font-size:12.5px;color:#444}
.plugin{left:822px;top:1032px;font-size:11.5px;color:#555;display:flex;align-items:center;gap:8px}
.plugin i{width:28px;height:28px;background:#3b5b94;border-radius:3px;display:block}

/* footer */
.dots{left:0;top:1083px;width:1200px;height:2px;border-top:2px dotted #d2d2d2}
.site-footer{left:0;top:1094px;width:1200px;height:43px;background:var(--footer)}
.footer-nav{left:52px;top:1108px;display:flex;gap:30px;font-size:11.5px;color:#ddd}
.copyright{right:64px;top:1106px;font-size:11.5px;color:#aaa}
</style>
</head>
<body>

<header class="abs site-header"></header>
<div class="abs brand">Medvora</div>
<div class="abs brand-rule"></div>
<div class="abs tagline">The Medical Peer Review</div>
<div class="abs quote">“Medvora keeps me ahead of the game, constantly testing my knowledge…”</div>
<div class="abs quote-source">--Ravi, doctor in training, Northgate University</div>
<div class="abs stats-line">How will your stats compare?</div>
<div class="abs social-icons" aria-label="Social links"><span></span><span></span><span></span><span></span><span></span><span></span><span></span><span></span><span></span></div>
<div class="abs field" style="top:56px">Username</div>
<div class="abs field" style="top:91px">Password</div>
<div class="abs remember"><i></i>Keep me signed in</div>
<div class="abs forgot">Forgot your Password?</div>
<div class="abs login-btn">Login</div>

<nav class="abs main-nav">
  <span>Home</span><span class="sep">—</span><span>Take The Tour</span><span class="sep">—</span><span>What Your Peers Say</span><span class="sep">—</span><span>Subscription Plans</span><span class="sep">—</span><span>Free Signup</span><span class="sep">—</span><span>Contact Us</span>
</nav>

<section class="abs hero"></section>
<div class="abs news-flash">about 2 days ago : Medvora is now on Circlebook. Follow us here</div>
<div class="abs share-square"></div>
<div class="abs share-btn" style="left:800px">Like</div>
<div class="abs count" style="left:867px">84</div>
<div class="abs share-btn" style="left:920px;padding:3px 6px">+1</div>
<div class="abs count" style="left:955px">2</div>
<div class="abs share-btn" style="left:1005px;width:84px;text-align:center">Chirp</div>
<div class="abs count" style="left:1093px;width:40px;text-align:center">11</div>

<h1 class="abs hero-title" style="font-weight:400">Medvora - The Medical Peer Review</h1>
<ul class="abs benefits">
  <li>-- Test your medical knowledge</li>
  <li>-- Answer a vast aray of medical questions</li>
  <li>-- Earn trophies as your knowledge increases</li>
  <li>-- Rate questions from peers</li>
  <li>-- Ask your own questions</li>
  <li>-- Link to your friends &amp; check their progress</li>
  <li>-- 29.903 Questions answered!</li>
</ul>

<svg class="abs arrow" style="left:64px" width="24" height="36" viewBox="0 0 24 36"><path d="M19 3 5 18l14 15" fill="none" stroke="#1a1a1a" stroke-width="6"/></svg>
<svg class="abs arrow" style="left:1109px" width="24" height="36" viewBox="0 0 24 36"><path d="M5 3l14 15L5 33" fill="none" stroke="#1a1a1a" stroke-width="6"/></svg>

<div class="abs photo" role="img" aria-label="Clipboard with a benefits note and a stethoscope" style="left:523px;top:321px;width:267px;height:179px;background:linear-gradient(135deg,#f2f2f2,#c9c9c9)"></div>
<div class="abs photo" role="img" aria-label="Pharmacist sorting medicine bottles on a counter" style="left:812px;top:321px;width:259px;height:179px;background:linear-gradient(135deg,#d9e6ee,#e8b46a 70%,#f4f4f4)"></div>
<div class="abs photo" role="img" aria-label="Researcher in scrubs working at a microscope" style="left:525px;top:519px;width:266px;height:175px;background:linear-gradient(135deg,#1f4f8c,#7fb3dc 60%,#e8eef3)"></div>
<div class="abs photo" role="img" aria-label="Doctor in a white coat writing on a clipboard" style="left:812px;top:519px;width:259px;height:175px;background:linear-gradient(135deg,#dfe6ea,#f5f7f8 60%,#b8c4cc)"></div>

<h2 class="abs box-head" style="left:58px;top:748px;width:344px;font-weight:400">How Medvora Works</h2>
<div class="abs video" role="img" aria-label="Introductory video player"></div>
<div class="abs video-bar"><span>▶</span><span class="track"></span><span>0:00 / 1:33</span><span>◀)</span><span>HQ</span></div>

<h2 class="abs box-head" style="left:459px;top:748px;width:310px;font-weight:400">Medvora Medical Peer Review</h2>
<div class="abs post" style="top:802px">
  <svg class="cal" viewBox="0 0 46 50" width="46" height="50"><rect x="1" y="5" width="44" height="44" rx="3" fill="#fff" stroke="#444"/><rect x="1" y="5" width="44" height="12" fill="#2e7fc4"/><rect x="10" y="1" width="4" height="9" fill="#555"/><rect x="32" y="1" width="4" height="9" fill="#555"/><text x="5" y="14" font-size="7" fill="#fff" font-family="Arial,sans-serif">SEP</text><text x="23" y="43" font-size="22" font-weight="700" text-anchor="middle" font-family="Arial,sans-serif" fill="#222">12</text></svg>
  <div><p>Lorem ipsum dolor sit amet, consectetur adipisicing elit, sed do eiusmod tempor incididunt ut labore et dolore magna aliqua.</p><span class="more">more+</span></div>
</div>
<div class="abs rule" style="left:455px;top:884px;width:314px"></div>
<div class="abs post" style="top:895px">
  <svg class="cal" viewBox="0 0 46 50" width="46" height="50"><rect x="1" y="5" width="44" height="44" rx="3" fill="#fff" stroke="#444"/><rect x="1" y="5" width="44" height="12" fill="#2e7fc4"/><rect x="10" y="1" width="4" height="9" fill="#555"/><rect x="32" y="1" width="4" height="9" fill="#555"/><text x="5" y="14" font-size="7" fill="#fff" font-family="Arial,sans-serif">SEP</text><text x="23" y="43" font-size="22" font-weight="700" text-anchor="middle" font-family="Arial,sans-serif" fill="#222">12</text></svg>
  <div><p>Lorem ipsum dolor sit amet, consectetur adipisicing elit,</p><span class="more">more+</span></div>
</div>
<div class="abs rule" style="left:455px;top:955px;width:314px"></div>
<div class="abs post" style="top:963px">
  <svg class="cal" viewBox="0 0 46 50" width="46" height="50"><rect x="1" y="5" width="44" height="44" rx="3" fill="#fff" stroke="#444"/><rect x="1" y="5" width="44" height="12" fill="#2e7fc4"/><rect x="10" y="1" width="4" height="9" fill="#555"/><rect x="32" y="1" width="4" height="9" fill="#555"/><text x="5" y="14" font-size="7" fill="#fff" font-family="Arial,sans-serif">SEP</text><text x="23" y="43" font-size="22" font-weight="700" text-anchor="middle" font-family="Arial,sans-serif" fill="#222">12</text></svg>
  <div><p>Lorem ipsum dolor sit amet, consectetur adipisicing elit,</p><span class="more">more+</span></div>
</div>
<div class="abs rule" style="left:455px;top:1028px;width:314px"></div>
<div class="abs join">Join the concersation <svg width="26" height="14" viewBox="0 0 26 14"><path d="M0 7h23M17 1l7 6-7 6" fill="none" stroke="#3a5f9a" stroke-width="2"/></svg></div>

<h2 class="abs box-head" style="left:832px;top:748px;width:305px;font-family:Arimo,Arial,sans-serif;font-size:15px;font-weight:700;padding-top:8px">Medvora on Circlebook</h2>
<div class="abs fans">22,0045 People Like Medvora</div>

<svg class="abs" style="left:837px;top:828px" width="300" height="180" viewBox="0 0 300 180">
  <g fill="#fff" stroke="#333" stroke-width="1">
    <rect x=".5" y=".5" width="55" height="55"/><rect x="60.5" y=".5" width="55" height="55"/><rect x="119.5" y=".5" width="55" height="55"/><rect x="181.5" y=".5" width="55" height="55"/><rect x="241.5" y=".5" width="55" height="55"/>
    <rect x=".5" y="96.5" width="55" height="55"/><rect x="60.5" y="96.5" width="55" height="55"/><rect x="119.5" y="96.5" width="55" height="55"/><rect x="181.5" y="96.5" width="55" height="55"/><rect x="241.5" y="96.5" width="55" height="55"/>
  </g>
  <g stroke="#333" stroke-width="1">
    <path d="M0 0l56 56M56 0 0 56M60 0l56 56M116 0 60 56M119 0l56 56M175 0l-56 56M181 0l56 56M237 0l-56 56M241 0l56 56M297 0l-56 56"/>
    <path d="M0 96l56 56M56 96 0 152M60 96l56 56M116 96l-56 56M119 96l56 56M175 96l-56 56M181 96l56 56M237 96l-56 56M241 96l56 56M297 96l-56 56"/>
  </g>
  <g font-family="Arimo,Arial,sans-serif" font-size="12.5" fill="#444">
    <text x="0" y="74">Name</text><text x="60" y="74">Name</text><text x="119" y="74">Name</text><text x="181" y="74">Name</text><text x="241" y="74">Name</text>
    <text x="0" y="170">Name</text><text x="60" y="170">Name</text><text x="119" y="170">Name</text><text x="181" y="170">Name</text><text x="241" y="170">Name</text>
  </g>
</svg>
<div class="abs rule" style="left:820px;top:1024px;width:315px"></div>
<div class="abs plugin"><i></i>Circlebook Social Plugin</div>

<div class="abs dots"></div>
<footer class="abs site-footer"></footer>
<nav class="abs footer-nav"><span>Home</span><span>Take The Tour</span><span>What Your Peers Say</span><span>Subscription Plans</span><span>Free Signup</span><span>Contact Us</span></nav>
<div class="abs copyright">© Copyright All Rights Reserved</div>

</body>
</html>
```